Kestrel Bathrooms Facelift. Moving the business in to the next professional level.

I'm currently revamping my bathroom renovation business. Part of this revamp includes our marketing strategy to better position ourselves as a professional business. As the name suggests, we primarily do bathroom renovations of all shapes, sizes and budgets. I'd like a business card design that is simple, yet displays our company as sophisticated.
What I'd like is to have a card that incorporates the following elements;
- Orange set as the primary colour and Charcoal/Grey as a complement colour. The card can also include white and/or black.
- I'd like a hexagon pattern within the charcoal/grey (In gloss perhaps to break it up a bit)
- I only want the Kestrel Bathrooms logo on the front of the card
- Back of the card would include contact details
- The bottom edges of the card would be rounded off
- I've attached the company name. I'd like to keep kestrel as it is. Bathrooms can be modified

```html
<!DOCTYPE html>
<html lang="en">
<head>
<meta charset="utf-8">
<title>Kestrel Bathrooms – Business Card</title>
<link rel="stylesheet" href="https://fonts.googleapis.com/css2?family=Quicksand:wght@300&family=Oswald:wght@600&family=Roboto:wght@400&family=Rajdhani:wght@500&display=swap">
<style>
  :root{
    --stage:#1c1c1c;
    --card:#ffffff;
    --card-shade:#ececec;
    --ink:#1a1a1a;
    --muted:#555555;
    --orange:#f26b1d;
    --charcoal:#2b2b2b;
    --charcoal-gloss:#4a4a4a;
    --on-band:#f2f2f2;
  }
  *{margin:0;padding:0;box-sizing:border-box}
  html,body{width:1200px;height:864px;overflow:hidden;background:var(--stage)}
  .stage{position:relative;width:1200px;height:864px}
  .card{
    position:absolute;width:560px;height:320px;
    background:linear-gradient(180deg,var(--card) 0%,var(--card-shade) 100%);
    overflow:hidden;
    border-radius:0 0 22px 22px;
    box-shadow:0 14px 30px rgba(0,0,0,.55);
  }
  .card--front{left:90px;top:90px}
  .card--back{left:550px;top:454px}

  .wordmark{position:absolute;font-family:"Quicksand",sans-serif;font-weight:300;color:var(--ink);line-height:1}
  .wordmark__name{display:block;letter-spacing:2px}
  .wordmark__sub{display:block;letter-spacing:1.5px;text-align:right}
  .card--front .wordmark{left:150px;top:108px}
  .card--front .wordmark__name{font-size:76px}
  .card--front .wordmark__sub{font-size:19px;margin-top:2px}
  .card--back .wordmark{left:272px;top:66px}
  .card--back .wordmark__name{font-size:64px}
  .card--back .wordmark__sub{font-size:16px;margin-top:2px}

  .front-rule{position:absolute;left:0;bottom:0;width:560px;height:10px;background:var(--orange)}

  .band{position:absolute;left:0;top:0;width:560px;height:320px}

  .person{position:absolute;left:26px;top:144px}
  .person__name{font-family:"Oswald",sans-serif;font-weight:600;font-size:20px;letter-spacing:.5px;color:var(--ink);line-height:1.1}
  .person__role{font-family:"Roboto",sans-serif;font-size:10px;letter-spacing:1.2px;color:var(--orange);margin-top:2px}

  .contacts{position:absolute;left:26px;top:194px;list-style:none}
  .contacts li{display:flex;align-items:center;gap:8px;height:15px;font-family:"Roboto",sans-serif;font-size:9.5px;color:var(--ink)}
  .contacts svg{width:9px;height:9px;flex:none}

  .address{
    position:absolute;left:262px;top:240px;width:284px;
    font-family:"Rajdhani",sans-serif;font-weight:500;font-size:14px;letter-spacing:.8px;
    color:var(--on-band);text-align:right;
  }
</style>
</head>
<body>
<main class="stage">

  <section class="card card--front" aria-label="Card front">
    <div class="wordmark">
      <span class="wordmark__name">kestrel</span>
      <span class="wordmark__sub">BATHROOMS</span>
    </div>
    <div class="front-rule"></div>
  </section>

  <section class="card card--back" aria-label="Card back">
    <svg class="band" viewBox="0 0 560 320" role="img" aria-label="Gloss charcoal band with hexagon pattern">
      <defs>
        <linearGradient id="gloss" x1="0" y1="0" x2="1" y2="1">
          <stop offset="0" stop-color="var(--charcoal-gloss)"/>
          <stop offset=".5" stop-color="var(--charcoal)"/>
          <stop offset="1" stop-color="#1e1e1e"/>
        </linearGradient>
      </defs>
      <path d="M0 284 H214 C236 284 236 214 262 214 H560 V320 H0 Z" fill="var(--orange)"/>
      <path d="M0 292 H220 C242 292 242 222 268 222 H560 V320 H0 Z" fill="url(#gloss)"/>
    </svg>

    <div class="wordmark">
      <span class="wordmark__name">kestrel</span>
      <span class="wordmark__sub">BATHROOMS</span>
    </div>

    <div class="person">
      <p class="person__name">DANA PRICE</p>
      <p class="person__role">GENERAL MANAGER</p>
    </div>

    <ul class="contacts">
      <li><svg viewBox="0 0 10 10"><path d="M2 1 L4 1 L4.6 3 L3.4 3.8 C4 5.2 4.8 6 6.2 6.6 L7 5.4 L9 6 L9 8 C5 8.6 1.4 5 2 1Z" fill="var(--orange)"/></svg>020 555 0143</li>
      <li><svg viewBox="0 0 10 10"><rect x="2.5" y=".5" width="5" height="9" rx="1" fill="var(--orange)"/><rect x="3.3" y="1.6" width="3.4" height="6" fill="#fff"/></svg>020 555 0144</li>
      <li><svg viewBox="0 0 10 10"><rect x="1" y="4" width="8" height="4" rx=".6" fill="var(--orange)"/><rect x="2.6" y="1" width="4.8" height="3" fill="var(--orange)"/></svg>020 555 0145</li>
      <li><svg viewBox="0 0 10 10"><rect x=".5" y="2" width="9" height="6" fill="var(--orange)"/><path d="M.8 2.3 L5 5.6 L9.2 2.3" fill="none" stroke="#fff" stroke-width=".8"/></svg>hello@kestrelbath.com</li>
      <li><svg viewBox="0 0 10 10"><circle cx="5" cy="5" r="4.3" fill="var(--orange)"/><path d="M.8 5 H9.2 M5 .8 C2.8 3 2.8 7 5 9.2 M5 .8 C7.2 3 7.2 7 5 9.2" fill="none" stroke="#fff" stroke-width=".6"/></svg>www.kestrelbath.com</li>
    </ul>

    <p class="address">14 Harbour Road, 3rd Floor, West</p>
  </section>

</main>
</body>
</html>
```